Corporate Business Card

Very professional, Modern, Not to busy, include phone address email, website
(253) 617-4930, 18761 52nd Avenue S, Kent, WA 98047, martin@plumlinegroup.com, varkoworks.com

Target Market(s)

Manufacturing

Industry/Entity Type

Aero, machining, manufacturing, Off road racing

Contact Information for Business Card

Phone, address email, website

```html
<!DOCTYPE html>
<html lang="en">
<head>
<meta charset="utf-8">
<title>Varko Works – Business Card</title>
<link href="https://fonts.googleapis.com/css2?family=Montserrat:wght@400;600;700&display=swap" rel="stylesheet">
<style>
  :root {
    --navy: #16346e;
    --red: #d42027;
    --white: #ffffff;
    --ink: #1c1c1c;
    --backdrop: #d6d6d6;
  }
  * { box-sizing: border-box; margin: 0; padding: 0; }
  html, body { width: 1200px; height: 813px; overflow: hidden; }
  body {
    background: var(--backdrop);
    font-family: "Montserrat", sans-serif;
    display: flex;
    align-items: center;
    justify-content: center;
    gap: 40px;
  }
  .card {
    position: relative;
    width: 560px;
    height: 320px;
    border-radius: 22px;
    overflow: hidden;
    box-shadow: 0 10px 28px rgba(0,0,0,0.28);
  }
  .card--front { background: var(--white); }
  .card--back { background: var(--navy); }

  .wave { position: absolute; inset: 0; width: 100%; height: 100%; }

  .brand {
    position: absolute;
    font-weight: 700;
    letter-spacing: 0.04em;
    text-transform: uppercase;
    white-space: nowrap;
  }
  .brand-rule { position: absolute; height: 2px; }

  .card--front .brand {
    left: 130px; top: 58px;
    font-size: 30px;
    color: var(--navy);
  }
  .card--front .brand-rule {
    left: 100px; top: 108px; width: 190px;
    background: var(--navy);
  }

  .contact {
    position: absolute;
    left: 34px; top: 168px;
    color: var(--ink);
    font-size: 13px;
    line-height: 1.45;
  }
  .contact__address { margin-bottom: 16px; }
  .contact__list { list-style: none; }
  .contact__item { display: flex; align-items: center; gap: 8px; }
  .contact__icon { width: 13px; height: 13px; flex: none; }

  .card--back .brand {
    left: 0; right: 0; top: 118px;
    text-align: center;
    font-size: 46px;
    color: var(--white);
  }
  .card--back .brand-rule {
    left: 85px; top: 190px; width: 200px;
    background: var(--white);
  }
</style>
</head>
<body>
  <section class="card card--front">
    <svg class="wave" viewBox="0 0 560 320" preserveAspectRatio="none" aria-hidden="true">
      <path d="M188 320 C 318 298 380 52 522 0 L560 0 L560 320 Z" fill="var(--red)"/>
      <path d="M212 320 C 338 300 396 58 542 0 L560 0 L560 320 Z" fill="var(--white)"/>
      <path d="M222 320 C 346 302 404 66 560 6 L560 320 Z" fill="var(--navy)"/>
    </svg>

    <div class="brand">Varko Works</div>
    <div class="brand-rule"></div>

    <div class="contact">
      <p class="contact__address">18761 52nd Avenue S<br>Kent, WA 98047</p>
      <ul class="contact__list">
        <li class="contact__item">
          <svg class="contact__icon" viewBox="0 0 16 16" aria-hidden="true"><path d="M4 1l3 3-2 2c1 2 3 4 5 5l2-2 3 3-2 3C7 15 1 9 1 3z" fill="var(--red)"/></svg>
          (253) 617-4930
        </li>
        <li class="contact__item">
          <svg class="contact__icon" viewBox="0 0 16 16" aria-hidden="true"><rect x="1" y="3" width="14" height="10" fill="var(--red)"/><path d="M1 3l7 6 7-6" fill="none" stroke="var(--white)" stroke-width="1.3"/></svg>
          martin@plumlinegroup.com
        </li>
        <li class="contact__item">
          <svg class="contact__icon" viewBox="0 0 16 16" aria-hidden="true"><circle cx="8" cy="8" r="7" fill="var(--red)"/><path d="M1 8h14M8 1c-3 4-3 10 0 14M8 1c3 4 3 10 0 14" fill="none" stroke="var(--white)" stroke-width="1"/></svg>
          www.varkoworks.com
        </li>
      </ul>
    </div>
  </section>

  <section class="card card--back">
    <div class="brand">Varko Works</div>
    <div class="brand-rule"></div>
  </section>
</body>
</html>
```